Design a single page Shopify store web page

We are looking to have a page designed for a single page Shopify store with 2 products. We already have a basic structure that we like, though we are open to suggestions. We are looking for somebody to provide a design/color scheme that we can then implement using Shopify's templating system. We can handle the implementation(HTML / CSS / jS) as we already have 2 web developers on the team, but have not been able to find a design we liked.

The job would consist of providing a mockup (photoshop or otherwise) and any vector graphics you choose to create for the site (we can provide product photos and other images).

You can also look at http://brickdune.com.au for some of our design direction we have used so far

Target Market(s)

Young Australian Males (18 - 49)

Industry/Entity Type

Store

Number of Pages Required

1 page

Font styles to use
Serif
Sans Serif

Requirements
Must have
• Single Page Design
• E-commerce Product Purchase
• Manly (whatever interpretation of that you have)

```html
<!DOCTYPE html>
<html lang="en">
<head>
<meta charset="utf-8">
<title>Brick Dune — Underwear &amp; Socks Plans</title>
<link rel="stylesheet" href="https://fonts.googleapis.com/css2?family=Open+Sans:wght@400;600;700&family=Orbitron:wght@400;500&display=swap">
<style>
:root{
  --green:#399b49;
  --green-dark:#2c7f3b;
  --green-pill:#3fa350;
  --ink:#1c1c1c;
  --ink-soft:#222;
  --text:#2a2a2a;
  --muted:#6b6b6b;
  --white:#ffffff;
}
*{box-sizing:border-box;margin:0;padding:0}
html,body{width:1200px;height:2317px;overflow:hidden}
body{position:relative;background:var(--white);font-family:"Open Sans",Arial,sans-serif;color:var(--text)}

/* Header */
.site-header{position:absolute;left:0;top:0;width:1200px;height:102px;background:var(--ink)}
.brand{position:absolute;left:139px;top:30px;display:flex;align-items:center;gap:14px;color:#cfcfcf;font-weight:600;font-size:34px;letter-spacing:2px;text-transform:uppercase}
.brand-dot{width:40px;height:40px;border-radius:50%;background:#cfcfcf}
.main-nav{position:absolute;left:579px;top:40px;display:flex;gap:32px}
.main-nav a{color:var(--white);text-decoration:none;font-size:12px;font-weight:600;text-transform:uppercase}
.signup-btn{position:absolute;left:954px;top:31px;width:104px;height:40px;border:1.5px solid var(--white);border-radius:3px;color:var(--white);font-size:12px;font-weight:600;display:flex;align-items:center;justify-content:center;text-transform:uppercase}

/* Hero */
.hero{position:absolute;left:0;top:102px;width:1200px;height:459px;background:var(--green);overflow:hidden}
.hero-photo{position:absolute;left:0;top:0;width:672px;height:459px}
.hero-title{position:absolute;left:703px;top:106px;white-space:nowrap;font-family:"Orbitron",sans-serif;font-weight:400;font-size:31px;letter-spacing:2px;line-height:40px;color:var(--ink);text-transform:uppercase}
.hero-lines{position:absolute;left:703px;top:170px;white-space:nowrap;color:var(--white);font-size:25px;font-weight:600;line-height:46px;text-transform:uppercase}
.hero-dots{position:absolute;left:710px;top:334px;display:flex;gap:7px}
.hero-dots span{width:10px;height:10px;border-radius:50%;background:var(--white)}
.hero-dots span.active{background:var(--ink)}

/* Section titles */
.section-title{position:absolute;left:0;width:1200px;text-align:center;font-size:28px;font-weight:700;text-transform:uppercase}

/* How it works */
.step{position:absolute;width:310px;text-align:center}
.step-icon{width:188px;height:188px;border-radius:50%;background:var(--green);margin:0 auto;display:flex;align-items:center;justify-content:center}
.step h3{margin-top:30px;font-size:20px;font-weight:700;color:var(--ink);text-transform:uppercase}
.step p{margin-top:20px;font-size:13px;line-height:20px;color:var(--muted)}

/* Plans */
.plans{position:absolute;left:0;top:1008px;width:1200px;height:601px;background:var(--green)}
.plans .section-title{color:var(--white);top:40px}
.plan{position:absolute;top:122px;width:460px}
.plan-name{color:var(--white);font-size:22px;font-weight:700;text-transform:uppercase}
.plan-card{position:absolute;top:34px;left:0;width:460px;height:281px;display:flex}
.plan-photo{width:281px;height:281px;border:2px solid var(--white)}
.plan-side{flex:1;background:var(--green-dark);padding:16px}
.plan-feature{height:49px;background:var(--green-pill);color:var(--white);font-size:13px;display:flex;align-items:center;justify-content:center;margin-bottom:17px}
.plan-price{color:var(--white);font-size:41px;font-weight:700;margin-top:-2px}
.plan-buy{margin-top:8px;height:55px;background:var(--ink);color:var(--white);font-size:24px;font-weight:600;display:flex;align-items:center;justify-content:center;border-radius:2px}
.perk{position:absolute;top:493px;height:51px;width:216px;background:var(--green-dark);display:flex;align-items:center;justify-content:center;gap:10px;color:var(--white);font-size:13px;font-weight:600}

/* FAQ */
.faq-item{position:absolute;width:270px;height:130px}
.faq-q{width:300px;display:flex;gap:12px;font-size:16px;font-weight:600;color:var(--ink-soft);text-transform:uppercase;line-height:25px}
.faq-mark{flex:none;width:20px;height:20px;border-radius:50%;background:var(--green);color:var(--white);font-size:12px;font-weight:700;display:flex;align-items:center;justify-content:center;margin-top:2px}
.faq-a{position:absolute;left:0;top:52px;width:270px;font-size:11px;line-height:23px;color:var(--muted);text-align:justify}

/* Footer */
.site-footer{position:absolute;left:0;top:2217px;width:1200px;height:100px;background:var(--ink);color:var(--white)}
.footer-links{position:absolute;left:142px;top:28px;font-size:12px}
.footer-copy{position:absolute;left:142px;top:56px;font-size:12px}
.social{position:absolute;top:29px;left:834px;display:flex;gap:14px}
.social span{width:34px;height:34px;border-radius:50%;border:2px solid var(--white)}
</style>
</head>
<body>

<header class="site-header">
  <div class="brand"><span class="brand-dot"></span>Brick Dune</div>
  <nav class="main-nav">
    <a href="#how">How it works</a>
    <a href="#plans">Plans</a>
    <a href="#faq">FAQ</a>
    <a href="#about">About us</a>
  </nav>
  <a class="signup-btn">Sign up now</a>
</header>

<section class="hero">
  <svg class="hero-photo" viewBox="0 0 672 459" role="img" aria-label="Photo of a man in dark briefs, sepia toned">
    <defs>
      <linearGradient id="heroTone" x1="0" y1="0" x2="1" y2="1">
        <stop offset="0" stop-color="#9a8672"/>
        <stop offset="1" stop-color="#4a3f35"/>
      </linearGradient>
    </defs>
    <polygon points="0,0 537,0 672,459 0,459" fill="url(#heroTone)"/>
  </svg>
  <h1 class="hero-title">Automate your life</h1>
  <p class="hero-lines">New underwear and socks<br>delivered to your door<br>when you need it</p>
  <div class="hero-dots"><span class="active"></span><span></span><span></span><span></span></div>
</section>

<h2 class="section-title" style="top:606px" id="how">How it works</h2>

<div class="step" style="left:135px;top:673px">
  <div class="step-icon">
    <svg width="80" height="80" viewBox="0 0 80 80"><polygon points="8,38 72,8 44,72 38,44" fill="#fff"/></svg>
  </div>
  <h3>Choose a plan</h3>
  <p>There will be plans for all budjets and styles.</p>
</div>
<div class="step" style="left:444px;top:673px">
  <div class="step-icon">
    <svg width="80" height="90" viewBox="0 0 80 90">
      <path d="M16 6h34l14 14v56H16z" fill="none" stroke="#fff" stroke-width="5" stroke-linejoin="round"/>
      <rect x="26" y="28" width="28" height="4" fill="#fff"/>
      <rect x="26" y="38" width="28" height="4" fill="#fff"/>
      <rect x="26" y="48" width="20" height="4" fill="#fff"/>
      <rect x="46" y="56" width="26" height="26" fill="#fff"/>
      <path d="M51 69l5 5 10-11" fill="none" stroke="#399b49" stroke-width="4"/>
    </svg>
  </div>
  <h3>Choose how often</h3>
  <p>Decide whether you would like to receve new<br>packages every 3 or 6 months</p>
</div>
<div class="step" style="left:748px;top:673px">
  <div class="step-icon">
    <svg width="80" height="80" viewBox="0 0 80 80">
      <rect x="8" y="26" width="64" height="14" fill="#fff"/>
      <rect x="13" y="43" width="54" height="31" fill="#fff"/>
      <rect x="36" y="26" width="8" height="48" fill="#399b49"/>
      <path d="M40 24c-6-14-22-14-18-4 2 4 10 4 18 4zM40 24c6-14 22-14 18-4-2 4-10 4-18 4z" fill="none" stroke="#fff" stroke-width="4"/>
    </svg>
  </div>
  <h3>Get your pack</h3>
  <p>We'll send out your first pack right away and<br>then again every 3 or 6 months</p>
</div>

<section class="plans" id="plans">
  <h2 class="section-title">Plans</h2>

  <div class="plan" style="left:140px">
    <div class="plan-name">Comfort</div>
    <div class="plan-card">
      <div class="plan-photo" role="img" aria-label="Photo of a man wearing white briefs" style="background:linear-gradient(160deg,#4a4643,#2a2725)"></div>
      <div class="plan-side">
        <div class="plan-feature">Consectetuer adip</div>
        <div class="plan-feature">Consectetuer adip</div>
        <div class="plan-price">$30</div>
        <div class="plan-buy">GET IT</div>
      </div>
    </div>
  </div>

  <div class="plan" style="left:621px">
    <div class="plan-name">Style</div>
    <div class="plan-card">
      <div class="plan-photo" role="img" aria-label="Photo of a man wearing striped trunks" style="background:linear-gradient(160deg,#5a4236,#1f1c1b)"></div>
      <div class="plan-side">
        <div class="plan-feature">Consectetuer adip</div>
        <div class="plan-feature">Consectetuer adip</div>
        <div class="plan-price">$30</div>
        <div class="plan-buy">GET IT</div>
      </div>
    </div>
  </div>

  <div class="perk" style="left:140px">
    <svg width="44" height="30" viewBox="0 0 44 30"><rect x="1" y="3" width="27" height="18" fill="#fff"/><path d="M29 9h8l6 7v5H29z" fill="#fff"/><circle cx="9" cy="24" r="4" fill="#fff" stroke="#2c7f3b" stroke-width="2"/><circle cx="35" cy="24" r="4" fill="#fff" stroke="#2c7f3b" stroke-width="2"/></svg>
    Free Shipping
  </div>
  <div class="perk" style="left:375px">
    <svg width="32" height="30" viewBox="0 0 32 30"><path d="M2 3h5l4 16h15l3-11H9" fill="none" stroke="#fff" stroke-width="2.5"/><circle cx="13" cy="25" r="2.5" fill="#fff"/><circle cx="24" cy="25" r="2.5" fill="#fff"/></svg>
    Easy Returns
  </div>
  <div class="perk" style="left:608px">
    <svg width="28" height="28" viewBox="0 0 28 28"><circle cx="14" cy="14" r="12" fill="#fff"/><path d="M9 9l10 10M19 9L9 19" stroke="#2c7f3b" stroke-width="3"/></svg>
    Cancel Whenever
  </div>
  <div class="perk" style="left:841px">
    <svg width="28" height="30" viewBox="0 0 28 30"><circle cx="14" cy="12" r="10" fill="none" stroke="#fff" stroke-width="3"/><circle cx="14" cy="12" r="4" fill="#fff"/><path d="M8 20l-2 9 8-4 8 4-2-9" fill="#fff"/></svg>
    Satisfaction Guaranteed
  </div>
</section>

<h2 class="section-title" style="top:1640px;color:var(--ink)" id="faq">FAQ</h2>

<div class="faq-item" style="left:142px;top:1712px">
  <div class="faq-q"><span class="faq-mark">?</span>What is Brick Dune ?</div>
  <p class="faq-a">Consectetuer adipiscing elit. Aenean commodo ligula eget dolor. Aenean massa. Cum sociis natoque penatibus et magnis dis parturient montes .</p>
</div>
<div class="faq-item" style="left:460px;top:1712px">
  <div class="faq-q"><span class="faq-mark">?</span>What is your satisfaction<br>guarantee ?</div>
  <p class="faq-a">Consectetuer adipiscing elit. Aenean commodo ligula eget dolor. Aenean massa. Cum sociis natoque penatibus et magnis dis parturient montes .</p>
</div>
<div class="faq-item" style="left:787px;top:1712px">
  <div class="faq-q"><span class="faq-mark">?</span>Shipping policy ?</div>
  <p class="faq-a">Consectetuer adipiscing elit. Aenean commodo ligula eget dolor. Aenean massa. Cum sociis natoque penatibus et magnis dis parturient montes .</p>
</div>

<div class="faq-item" style="left:142px;top:1873px">
  <div class="faq-q"><span class="faq-mark">?</span>What do I get with my<br>Brick Dune plan?</div>
  <p class="faq-a">Consectetuer adipiscing elit. Aenean commodo ligula eget dolor. Aenean massa. Cum sociis natoque penatibus et magnis dis parturient montes .</p>
</div>
<div class="faq-item" style="left:460px;top:1873px">
  <div class="faq-q"><span class="faq-mark">?</span>Returns policy</div>
  <p class="faq-a">Consectetuer adipiscing elit. Aenean commodo ligula eget dolor. Aenean massa. Cum sociis natoque penatibus et magnis dis parturient montes .</p>
</div>
<div class="faq-item" style="left:787px;top:1873px">
  <div class="faq-q"><span class="faq-mark">?</span>What brands do you<br>stock ?</div>
  <p class="faq-a">Consectetuer adipiscing elit. Aenean commodo ligula eget dolor. Aenean massa. Cum sociis natoque penatibus et magnis dis parturient montes .</p>
</div>

<div class="faq-item" style="left:142px;top:2041px">
  <div class="faq-q"><span class="faq-mark">?</span>What is your cancellation<br>policy?</div>
  <p class="faq-a">Consectetuer adipiscing elit. Aenean commodo ligula eget dolor. Aenean massa. Cum sociis natoque penatibus et magnis dis parturient montes .</p>
</div>
<div class="faq-item" style="left:460px;top:2041px">
  <div class="faq-q"><span class="faq-mark">?</span>What about sizing?</div>
  <p class="faq-a">Consectetuer adipiscing elit. Aenean commodo ligula eget dolor. Aenean massa. Cum sociis natoque penatibus et magnis dis parturient montes .</p>
</div>
<div class="faq-item" style="left:787px;top:2041px">
  <div class="faq-q"><span class="faq-mark">?</span>How does payment work?</div>
  <p class="faq-a">Consectetuer adipiscing elit. Aenean commodo ligula eget dolor. Aenean massa. Cum sociis natoque penatibus et magnis dis parturient montes .</p>
</div>

<footer class="site-footer">
  <div class="footer-links">Shipping &nbsp;|&nbsp; Returns &nbsp;|&nbsp; Payment &nbsp;|&nbsp; Terms &nbsp;|&nbsp; Privacy</div>
  <div class="footer-copy">Copy right 2014 brickdune.com &nbsp;|&nbsp; All rights reserved</div>
  <div class="social" aria-label="Social links"><span></span><span></span><span></span><span></span><span></span></div>
</footer>

</body>
</html>
```